Cover Art Design for a Notebook

We are going to give away some note books to our marketing department and want an elegant art design for the cover. There is a theme centered around ABCD of marketing that we want to leverage in the design. So these letters should be prominent in the design. The ABCD stand for Agility, Boost, Customer, Data.

If you could Cleverly incorporate these words into the letters with a good design that would be good.

But please make the ABCD the focus of the artwork. The words associated with them should be subtle, in the background, visible but not the focus.

We are looking for stylish. We want people to feel proud of the ELEGANT DESIGN when they take out this notebook for business.

Also worth mentioning- We are a biotechnology company so if you incorporate elements in that theme in, on, or around the ABCD letters, it could be a good idea. As long as it doesn’t kill the rest of the design.

I will upload our logo for Kelvara Biolume Sciences later (you can see it online) and this will need to go in one corner.

Notebook will be A5 format. Image on front cover only. Need ASAP.

(Do not make baby blocks as we don’t want something that looks like a kids book)

Target Market(s)

business people who feel proud to pull out this notebook

Industry/Entity Type

Biotechnology

Colors
ec1f27
ffffff
000000

Requirements
Must have
• ELEGANT ART DESIGN USING ABCD
Nice to have
• see brief above
Should not have
• baby blocks

```html
<!DOCTYPE html>
<html lang="en">
<head>
<meta charset="UTF-8">
<title>ABCD of Marketing — Notebook Cover</title>
<link rel="stylesheet" href="https://fonts.googleapis.com/css2?family=Arimo:wght@400&display=swap">
<style>
  :root {
    --brand-red: #ec1f27;
    --ink: #1a1a1a;
    --white: #ffffff;
    --teal: #3fb8bb;
    --deep-blue: #1f4f6b;
    --mist: #eef0ee;
    --blush: #f3c9cf;
    --amber: #e9a46a;
    --rose: #f0a9b8;
    --cell-fill: rgba(255, 255, 255, 0.28);
  }
  * { margin: 0; padding: 0; box-sizing: border-box; }
  html, body { width: 846px; height: 1200px; overflow: hidden; }
  body { font-family: "Arimo", Arial, sans-serif; background: var(--white); }

  .cover { position: relative; width: 846px; height: 1200px; overflow: hidden; }

  .lab-scene {
    position: absolute; inset: 0;
    background:
      radial-gradient(ellipse 520px 300px at 80% 6%, rgba(31, 79, 107, 0.85), transparent 70%),
      radial-gradient(ellipse 420px 320px at 8% 22%, rgba(63, 184, 187, 0.9), transparent 70%),
      radial-gradient(ellipse 260px 160px at 95% 50%, rgba(217, 120, 170, 0.55), transparent 70%),
      radial-gradient(ellipse 700px 330px at 50% 100%, rgba(240, 169, 184, 0.9), transparent 70%),
      radial-gradient(ellipse 520px 200px at 40% 95%, rgba(233, 164, 106, 0.7), transparent 70%),
      linear-gradient(180deg, var(--teal) 0%, #7fcfcf 22%, var(--mist) 48%, #f4ecea 66%, var(--blush) 84%, var(--rose) 100%);
  }

  .brand {
    position: absolute; top: 108px; left: 0; width: 846px;
    display: flex; justify-content: center; align-items: center; gap: 12px;
    color: var(--white); font-weight: 400; font-size: 30px; line-height: 1;
  }
  .brand-mark { width: 14px; height: 14px; background: var(--white); }

  .abcd-grid {
    position: absolute; left: 147px; top: 194px; width: 552px; height: 552px;
    display: grid; grid-template-columns: 1fr 1fr; grid-template-rows: 1fr 1fr;
    border: 3px solid var(--brand-red);
  }
  .cell {
    position: relative; background: var(--cell-fill);
    border: 1.5px solid var(--brand-red);
  }
  .letter {
    position: absolute; top: 2px; right: 18px;
    font-size: 164px; line-height: 1; color: var(--brand-red); font-weight: 400;
  }
  .cell-a .letter { right: 22px; }
  .cell-b .letter { right: 12px; }
  .word {
    position: absolute; left: 20px;
    font-size: 60px; line-height: 1; color: var(--ink); letter-spacing: -1px;
  }
  .cell-a .word { bottom: 14px; }
  .cell-b .word { bottom: 8px; }
  .cell-c .word { left: 11px; bottom: 6px; letter-spacing: -2px; }
  .cell-d .word { bottom: 10px; }
</style>
</head>
<body>
  <main class="cover">
    <div class="lab-scene" role="img" aria-label="Soft-focus laboratory photograph: a pipette tip dispensing into a multi-well plate under teal and pink light"></div>

    <header class="brand">
      <span class="brand-mark" aria-hidden="true"></span>
      <span class="brand-name">Kelvara Biolume Sciences</span>
    </header>

    <section class="abcd-grid" aria-label="ABCD of marketing">
      <div class="cell cell-a"><span class="letter">A</span><span class="word">Agile</span></div>
      <div class="cell cell-b"><span class="letter">B</span><span class="word">Boost</span></div>
      <div class="cell cell-c"><span class="letter">C</span><span class="word">Customer</span></div>
      <div class="cell cell-d"><span class="letter">D</span><span class="word">Data</span></div>
    </section>
  </main>
</body>
</html>
```